Need a website where people can find information about the newly formed Northmere Valuation Oversight Board. Soon after, we will need a place to publish our findings as we audit each municipality in the State of Wisconsin. I have a logo (designed by Artwell Hub), a MS Word document showing the content and a set of images to choose from that we can purchase from Pixmarla.com (found here https://www.pixmarla.com/collaboration/boards/-Xq7TbLwRmNoPzYkAuH-Jd)

```html
<!DOCTYPE html>
<html lang="en">
<head>
<meta charset="utf-8">
<title>Northmere Valuation Oversight Board</title>
<link href="https://fonts.googleapis.com/css2?family=Archivo:wght@600;700;800&family=Inter:wght@400;500;600;700&display=swap" rel="stylesheet">
<style>
:root{
  --green:#3a7a17;
  --green-dark:#2f6512;
  --mint:#effde6;
  --ink:#111111;
  --text:#3b3b3b;
  --white:#ffffff;
  --footer:#141414;
  --line:#d8d8d8;
}
*{box-sizing:border-box;margin:0;padding:0}
html,body{width:1200px;height:4612px;overflow:hidden}
body{font-family:"Inter",Arial,sans-serif;color:var(--text);background:var(--white);position:relative}
section,header,footer{position:absolute;left:0;width:1200px}
.abs{position:absolute}
h2{font-family:"Archivo",Arial,sans-serif;font-weight:700;color:var(--ink);text-transform:uppercase;line-height:1.15}
.body-copy{font-size:13px;line-height:30px;color:var(--text);letter-spacing:-0.1px}
.btn{display:inline-block;border-radius:22px;font-weight:700;font-size:15px;text-transform:uppercase;padding:0 26px;height:42px;line-height:42px;text-decoration:none}
.btn-green{background:var(--green);color:var(--white)}
.btn-outline{border:1.5px solid var(--white);color:var(--white);line-height:39px}
.photo{border-radius:14px}

/* header */
.hero{top:0;height:720px;background:linear-gradient(180deg,#1d5fb8 0%,#4d8ed8 35%,#c9ccc6 60%,#8a8c7e 75%,#3f6e24 100%)}
.brand{left:110px;top:24px;display:flex;align-items:center;gap:10px}
.brand-mark{width:22px;height:22px;background:var(--green)}
.brand-name{font-family:"Inter",sans-serif;font-weight:700;color:var(--white);font-size:22px}
.nav{left:306px;top:76px;display:flex;gap:28px;font-size:14.5px;font-weight:600;color:var(--white)}
.top-btns{right:112px;top:18px;display:flex;gap:20px}
.top-btns .btn{height:38px;line-height:38px;font-size:14px;padding:0 32px}
.btn-contact{border:2px solid var(--white);color:var(--white);line-height:34px!important}
.hero-title{left:305px;top:468px;width:592px;height:160px;background:rgba(58,122,23,.88);border:3px solid rgba(255,255,255,.6);display:flex;align-items:center;justify-content:center;text-align:center}
.hero-title h1{font-family:"Archivo",Arial,sans-serif;font-weight:800;color:var(--white);font-size:34px;line-height:44px;text-transform:uppercase}

/* who we are */
.who{top:720px;height:637px}
.who-mark{left:120px;top:130px;width:455px;display:flex;align-items:center;gap:18px}
.who-mark .sq{width:110px;height:110px;background:var(--green);flex:none}
.who-mark span{font-family:"Inter",sans-serif;font-weight:700;color:var(--green);font-size:34px;line-height:42px}
.who h2{left:644px;top:80px;font-size:38px}
.who .body-copy{left:644px;top:142px;width:450px}
.who .btn{left:640px;top:495px}

/* problem */
.problem{top:1357px;height:570px}
.problem-panel{left:0;top:0;width:600px;height:570px;background:var(--green)}
.problem h2{left:111px;top:66px;color:var(--white);font-size:29px;line-height:46px;width:460px}
.problem .body-copy{left:111px;top:168px;width:440px;color:var(--white);font-size:12.5px;line-height:27px}
.problem .link{text-decoration:underline;word-break:break-all;display:block;margin:10px 0}
.problem .btn{left:111px;top:453px}
.problem-img{left:600px;top:0;width:600px;height:570px;background:linear-gradient(135deg,#8fb6c9 0%,#c9b28b 40%,#c68b3e 70%,#e7e4dc 100%)}

/* results */
.results{top:1927px;height:575px;background:var(--mint)}
.results h2{left:0;width:1200px;text-align:center;top:65px;font-size:34px}
.results .intro{left:200px;width:800px;top:126px;text-align:center;font-size:15px;line-height:33px}
.audit-table{position:absolute;left:111px;top:221px;width:979px;border-collapse:collapse;background:var(--white);font-size:15.5px}
.audit-table th{background:var(--green);color:var(--white);font-weight:700;height:56px;border:1px solid #5f9a3f}
.audit-table td{height:52px;border:1px solid var(--line);padding-left:17px;color:#222}
.audit-table td.c{text-align:center;padding-left:0}

/* uniform */
.uniform{top:2502px;height:600px}
.uniform .back{left:118px;top:90px;width:448px;height:470px;background:var(--green);border-radius:14px}
.uniform .photo{left:136px;top:108px;width:446px;height:440px;background:linear-gradient(160deg,#6f8a4e 0%,#8aa06a 40%,#b6b4a6 70%,#5e7343 100%)}
.uniform h2{left:636px;top:100px;font-size:38px;line-height:46px}
.uniform .body-copy{left:636px;top:200px;width:450px;font-size:12.4px;text-align:justify}
.uniform .btn{left:632px;top:506px}

/* methods */
.methods{top:3102px;height:600px}
.methods h2{left:122px;top:52px;font-size:38px}
.methods .body-copy{left:122px;top:120px;width:450px}
.methods .btn{left:118px;top:438px}
.methods .back{left:635px;top:40px;width:446px;height:455px;background:var(--green);border-radius:14px}
.methods .photo{left:618px;top:58px;width:446px;height:437px;background:radial-gradient(circle at 45% 45%,#d4d4d4 0%,#8a8a8a 45%,#3a3a3a 100%)}

/* contact */
.contact{top:3702px;height:536px;background:var(--green)}
.contact h2{left:0;width:1200px;text-align:center;top:68px;color:var(--white);font-size:38px}
.contact .intro{left:300px;width:600px;top:122px;text-align:center;color:var(--white);font-size:13.5px;line-height:24px}
.field{position:absolute;background:var(--white);height:38px;font-size:11px;color:#555;padding:12px 14px;display:flex;gap:6px;align-items:flex-start}
.field svg{width:10px;height:10px;flex:none;margin-top:1px}
.submit{left:508px;top:416px;width:184px;height:52px;border-radius:26px;background:var(--white);color:var(--green);font-weight:700;font-size:16px;text-align:center;line-height:52px}

/* footer */
.site-footer{top:4238px;height:374px;background:var(--footer);color:var(--white)}
.f-brand{left:120px;top:112px;display:flex;align-items:center;gap:8px}
.f-brand .sq{width:22px;height:22px;background:var(--green)}
.f-brand span{font-weight:700;font-size:22px}
.socials{left:130px;top:228px;display:flex;gap:7px}
.socials i{width:30px;height:30px;border-radius:50%;background:var(--white);display:block}
.f-col h3{font-family:"Archivo",sans-serif;font-size:15px;font-weight:700;text-transform:uppercase;letter-spacing:.3px;display:inline-block}
.f-col .rule{width:50px;height:2px;background:var(--white);margin:8px 0 14px}
.f-col ul{list-style:none;font-size:12px;line-height:28px}
.f-item{display:flex;gap:14px;font-size:12px;line-height:22px;margin-bottom:18px;align-items:flex-start}
.f-item .ic{width:26px;height:26px;border-radius:50%;background:#2a2a2a;flex:none;display:flex;align-items:center;justify-content:center}
.subscribe{width:262px;height:46px;background:var(--white);border-radius:23px;margin-top:24px;position:relative;font-size:12px;color:#777;padding:15px 0 0 20px}
.subscribe .go{position:absolute;right:2px;top:1px;width:44px;height:44px;border-radius:50%;background:var(--green)}
.copyright{left:111px;top:306px;width:979px;border-top:1px solid #333;text-align:center;font-size:12px;padding-top:28px}
</style>
</head>
<body>

<header class="hero">
  <div class="abs" role="img" aria-label="State capitol building with dome under a blue sky" style="left:0;top:0;width:1200px;height:720px"></div>
  <div class="abs brand"><span class="brand-mark"></span><span class="brand-name">NVOB</span></div>
  <nav class="abs nav">
    <span>Who We Are</span><span>Non-Uniform Property Tax Problem</span><span>What is Uniform Taxation?</span><span>Blog</span><span>More ▾</span>
  </nav>
  <div class="abs top-btns"><span class="btn btn-green">Donate</span><span class="btn btn-contact">Contact Us</span></div>
  <div class="abs hero-title"><h1>Northmere Valuation<br>Oversight Board</h1></div>
</header>

<section class="who">
  <div class="abs who-mark"><span class="sq"></span><span>Northmere Valuation Oversight Board</span></div>
  <h2 class="abs">Who We Are</h2>
  <p class="abs body-copy">We audit each municipalities' electronic property tax assessment records. Municipalities are required to keep their assessment records in electronic form, but some do not because the Department of Revenue, who made up the requirement, doesn't enforce their own administrative rules. Not understanding what the word "requirement" means is a longstanding problem at the Department of Revenue and one of the many causes of non-uniformity. Problem with uniformity can nearly always be tracked back to problem with assessed values. Most real estate in Wisconsin is supposed to be assessed at 100% of market value. The largest exceptions are agricultural land, land in DNR forest programs and exempt property.</p>
  <span class="abs btn btn-green">Learn More</span>
</section>

<section class="problem">
  <div class="abs problem-panel"></div>
  <h2 class="abs">Wisconsin's Non-Uniform Property Tax Problem</h2>
  <div class="abs body-copy">
    <p>Article VIII Section 1 of the State Constitution states that all taxation shall be uniform. Non-uniform taxation is a statewide epidemic. For proof of this, see the results of this watchdog investigation done by the Lakeshore Daily Ledger.</p>
    <span class="link">https://archive.lakeshoreledger.com/watchdog/reports/across-the-state-uneven-property-assessments-fly-in-the-face-of-fairness-418203577.html</span>
    <p>Too many property taxes in the State of Wisconsin are not uniform. Non-uniform taxes are unjust and unfair.</p>
  </div>
  <span class="abs btn btn-outline">Learn More</span>
  <div class="abs problem-img" role="img" aria-label="Property tax note pinned over a parcel map beside a tree in a wheat field"></div>
</section>

<section class="results">
  <h2 class="abs">Who Passed &amp; Who Failed</h2>
  <p class="abs intro">We are just getting started with our audits. This list of who passed and who failed will be updated regularly as we finish large chunks of work.</p>
  <table class="audit-table">
    <colgroup><col style="width:128px"><col style="width:181px"><col style="width:163px"><col style="width:154px"><col></colgroup>
    <thead><tr><th>County</th><th>Municipality</th><th>Year Audited</th><th>Audit Result</th><th>Municipal Response</th></tr></thead>
    <tbody>
      <tr><td>Ashland</td><td>Town of Morse</td><td class="c">2021</td><td>Fail</td><td></td></tr>
      <tr><td>Ashland</td><td>Town of White River</td><td class="c">2021</td><td>Fail</td><td></td></tr>
      <tr><td>Price</td><td>Town of Elk</td><td class="c">2021</td><td>Fail</td><td></td></tr>
      <tr><td>Taylor</td><td>Town of Hammel</td><td class="c">2021</td><td>Fail</td><td></td></tr>
    </tbody>
  </table>
</section>

<section class="uniform">
  <div class="abs back"></div>
  <div class="abs photo" role="img" aria-label="Aerial view of a suburban neighborhood with houses and trees"></div>
  <h2 class="abs">What is Uniform<br>Taxation?</h2>
  <p class="abs body-copy">Uniform taxation means similar properties have similar values for taxation purposes. For example, if you own a condominium assessed for tax purposes at $200,000 and your neighbor has the same unit but is assessed at $160,000, your values, and therefore your taxes, will be significantly different. You will be paying more of the tax burden than your neighbor, even though the market value of both units is the same. This is non-uniform taxation. Two properties are often not identical; but to the extent that they are the same their assessed values should be the same. To the extent they are different their assessed values should be different.</p>
  <span class="abs btn btn-green">Learn More</span>
</section>

<section class="methods">
  <h2 class="abs">Audit Methods</h2>
  <p class="abs body-copy">We audit each municipalities' electronic property tax assessment records. Municipalities are required to keep their assessment records in electronic form, but some do not because the Department of Revenue, who made up the requirement, doesn't enforce their own administrative rules. Not understanding what the word "requirement" means is a longstanding problem at the Department of Revenue and one of the many causes of non-uniformity.<br>Problem with uniformity can nearly always be tracked back to problem with assessed values. Most real estate in Wisconsin is supposed to be assessed at 100% of market value.</p>
  <span class="abs btn btn-green">Learn More</span>
  <div class="abs back"></div>
  <div class="abs photo" role="img" aria-label="Metal gears engraved with the words audit, review and asset"></div>
</section>

<section class="contact">
  <h2 class="abs">Contact Us</h2>
  <p class="abs intro">If you would like to contact us in order to file a complaint about non-uniform assessments or you have a comment or question, please use the following:</p>
  <div class="field" style="left:180px;top:190px;width:412px"><svg viewBox="0 0 10 10"><circle cx="5" cy="3" r="2.5" fill="#555"/><path d="M0 10a5 4 0 0 1 10 0z" fill="#555"/></svg>First Name</div>
  <div class="field" style="left:609px;top:190px;width:412px"><svg viewBox="0 0 10 10"><circle cx="5" cy="3" r="2.5" fill="#555"/><path d="M0 10a5 4 0 0 1 10 0z" fill="#555"/></svg>Last Name</div>
  <div class="field" style="left:180px;top:242px;width:412px"><svg viewBox="0 0 10 10"><rect x="2" y="0" width="6" height="10" fill="#555"/></svg>Company</div>
  <div class="field" style="left:180px;top:294px;width:412px"><svg viewBox="0 0 10 10"><rect x="0" y="2" width="10" height="7" fill="none" stroke="#555" stroke-width="1.5"/><path d="M0 2l5 4 5-4" fill="none" stroke="#555"/></svg>Email Address</div>
  <div class="field" style="left:180px;top:346px;width:412px"><svg viewBox="0 0 10 10"><path d="M2 0l2 3-1 1q1 2 3 3l1-1 3 2-2 2Q1 9 0 2z" fill="#555"/></svg>Phone Number</div>
  <div class="field" style="left:609px;top:242px;width:412px;height:142px"><svg viewBox="0 0 10 10"><ellipse cx="5" cy="4" rx="5" ry="3.5" fill="#555"/></svg>How can I help you? :</div>
  <div class="abs submit">SUBMIT</div>
</section>

<footer class="site-footer">
  <div class="abs f-brand"><span class="sq"></span><span>NVOB</span></div>
  <div class="abs socials"><i></i><i></i><i></i><i></i></div>
  <div class="abs f-col" style="left:358px;top:72px">
    <h3>Quick Links</h3><div class="rule"></div>
    <ul><li>Who We Are</li><li>Wisconsin's Non-Uniform</li><li>Property Tax Problem</li><li>What is Uniform Taxation?</li><li>Blog</li><li>More</li></ul>
  </div>
  <div class="abs f-col" style="left:561px;top:72px;width:200px">
    <h3>Contact Us</h3><div class="rule"></div>
    <div class="f-item"><span class="ic"><svg width="10" height="12" viewBox="0 0 10 12"><path d="M5 0a4 4 0 0 1 4 4c0 3-4 8-4 8S1 7 1 4a4 4 0 0 1 4-4z" fill="#fff"/></svg></span><span>123 Avenue name, City name 10150, United States</span></div>
    <div class="f-item"><span class="ic"><svg width="10" height="10" viewBox="0 0 10 10"><path d="M2 0l2 3-1 1q1 2 3 3l1-1 3 2-2 2Q1 9 0 2z" fill="#fff"/></svg></span><span>+1 888 888 8888</span></div>
    <div class="f-item"><span class="ic"><svg width="11" height="9" viewBox="0 0 11 9"><rect x=".5" y=".5" width="10" height="8" fill="none" stroke="#fff"/><path d="M.5 .5l5 4 5-4" fill="none" stroke="#fff"/></svg></span><span>info@nvob.org</span></div>
  </div>
  <div class="abs f-col" style="left:823px;top:72px;width:270px">
    <h3>Subscribe to our Blog</h3><div class="rule"></div>
    <p style="font-size:12px;line-height:27px">Sign up today to get resources on how to attract and retain more customers!</p>
    <div class="subscribe">✉ Email Address<span class="go"><svg width="44" height="44" viewBox="0 0 44 44"><path d="M14 22l16-7-6 16-3-6z" fill="#fff"/></svg></span></div>
  </div>
  <div class="abs copyright">©Copyright ©2021 NVOB. All Rights Reserved.</div>
</footer>

</body>
</html>
```